Harborview Estates Business Card for Apartment Buildings

Create business cards for resident managers who run apartment buildings. The audience is the public who are searching for apartment rentals, and current residents who live at the apartment building. Key design element will be incorporating the company logo, however, the logo cannot dominate. The building name and manager name are more important than the logo. Current business card design leaves little room for copy, so we may need to reduce the size on the current card to allow for more space for copy.

Target Market(s)

Adults 18-65 years of age, who are looking for an apartment rental, plus current residents who live at our apartment buildings.

Industry/Entity Type

Property Management

Contact Information for Business Card

A major design element will be use of the company logo. Important property and manager contact information must be part of the design. The size of the logo will need to be reduced to make room for building and manager contact copy.

Font styles to use
Sans Serif

Colors
3176b5
000000
959595
ffffff

Requirements
Must have
• 1) Incorporate the company logo.
• 2) Use the company colors (dark blue, black/grey, over white).
• 3) FEATURE THE BUILDING NAME
• 4) FEATURE THE MANAGER NAME
• 5) The company name is less important than BUILDING and MANAGER
• 6) Manager contact information
• **SEE ATTACHED CREATIVE BRIEF**
Nice to have
• 1) Back of card logo watermark
• 2) Ability to write notes on back of carfd
Should not have
• Avoid letting the company logo dominate the card, the building name and manager are more important than the company logo.

```html
<!DOCTYPE html>
<html lang="en">
<head>
<meta charset="utf-8">
<title>Harborview Estates – Resident Manager Business Card</title>
<link rel="stylesheet" href="https://fonts.googleapis.com/css2?family=Montserrat:wght@600;700&family=Roboto:wght@400&family=Roboto+Condensed:wght@700&display=swap">
<style>
  :root {
    --brand-blue: #1f66a6;
    --ink-grey: #454545;
    --text-grey: #4a4a4a;
    --card-white: #f2f2f2;
    --backdrop: #262626;
    --watermark: #e3e3e3;
  }
  * { margin: 0; padding: 0; box-sizing: border-box; }
  html, body {
    width: 1200px; height: 960px; overflow: hidden;
    background: var(--backdrop);
  }
  .card {
    position: absolute;
    width: 600px; height: 343px;
    background: var(--card-white);
    box-shadow: 0 3px 8px rgba(0,0,0,.5);
  }
  .card--front { left: 314px; top: 113px; }
  .card--back  { left: 311px; top: 472px; }

  .side-band {
    position: absolute; left: 0; top: 0;
    width: 24px; height: 100%;
    background: var(--brand-blue);
  }
  .band-notch { position: absolute; left: 0; top: 0; }

  .manager {
    position: absolute; left: 61px; top: 48px;
    font-family: "Montserrat", sans-serif;
  }
  .manager__name {
    font-size: 21px; font-weight: 700; color: var(--brand-blue);
    letter-spacing: .3px; line-height: 1.1;
  }
  .manager__title {
    font-size: 14px; font-weight: 700; color: var(--ink-grey);
    letter-spacing: .4px; margin-top: 3px;
  }

  .property {
    position: absolute; left: 61px; top: 130px;
    font-family: "Roboto", sans-serif;
  }
  .property__name {
    font-family: "Roboto Condensed", sans-serif;
    font-size: 21px; font-weight: 700; color: var(--brand-blue);
    line-height: 1.2;
  }
  .property__address {
    font-size: 14px; color: var(--text-grey); line-height: 18px;
  }

  .contact-list {
    position: absolute; left: 61px; top: 210px;
    list-style: none;
    font-family: "Roboto", sans-serif; font-size: 14px; color: var(--text-grey);
  }
  .contact-list li {
    display: flex; align-items: center; height: 19px;
  }
  .contact-list svg { width: 13px; height: 13px; margin-right: 9px; fill: var(--brand-blue); }

  .company-mark {
    position: absolute; left: 330px; top: 255px;
    display: flex; align-items: center; gap: 8px;
  }
  .company-mark__square { width: 18px; height: 18px; background: var(--brand-blue); }
  .company-mark__name {
    font-family: "Montserrat", sans-serif; font-size: 19px; font-weight: 700;
    color: var(--brand-blue); letter-spacing: .2px;
  }

  .back-watermark {
    position: absolute; inset: 0;
    display: flex; align-items: center; justify-content: center;
    font-family: "Montserrat", sans-serif; font-size: 44px; font-weight: 700;
    color: var(--watermark); letter-spacing: 1px;
  }
</style>
</head>
<body>

<section class="card card--front" aria-label="Business card front">
  <div class="side-band"></div>
  <svg class="band-notch" width="24" height="82" viewBox="0 0 24 82" aria-hidden="true">
    <path d="M6 0 V74 L20 66 V0" fill="#3a3a3a" stroke="#ffffff" stroke-width="2"/>
  </svg>

  <div class="manager">
    <h1 class="manager__name">MARISOL WHITAKER</h1>
    <p class="manager__title">RESIDENT MANAGER</p>
  </div>

  <div class="property">
    <h2 class="property__name">Cedar Glen Apartments</h2>
    <p class="property__address">1458 Linden Avenue<br>Brookhaven, CA 92870</p>
  </div>

  <ul class="contact-list">
    <li><svg viewBox="0 0 16 16"><path d="M3 1l3 3-1.5 2c1 2 2.5 3.5 4.5 4.5L11 9l3 3-2 3C6 14 2 10 1 3z"/></svg>555-214-3380</li>
    <li><svg viewBox="0 0 16 16"><path d="M4 0h8v16H4zM5.5 2v10h5V2zM7 13.5h2v1H7z" fill-rule="evenodd"/></svg>555-871-4402</li>
    <li><svg viewBox="0 0 16 16"><path d="M4 1h8v4H4zM1 6h14v6h-2v3H3v-3H1zM4 10v4h8v-4z" fill-rule="evenodd"/></svg>555-639-1175</li>
    <li><svg viewBox="0 0 16 16"><path d="M1 3h14v10H1zM2 4l6 5 6-5z" fill-rule="evenodd"/></svg>marisol@harborviewest.com</li>
    <li><svg viewBox="0 0 16 16"><circle cx="8" cy="8" r="7"/></svg>www.harborviewest.com</li>
  </ul>

  <div class="company-mark">
    <span class="company-mark__square"></span>
    <span class="company-mark__name">Harborview Estates LLC</span>
  </div>
</section>

<section class="card card--back" aria-label="Business card back">
  <div class="back-watermark">Harborview Estates</div>
</section>

</body>
</html>
```